Business Card Design

We provide services doing multiple jobs in the construction industry.Please note: The company name needs to be ROCK SOLID BUILDING SERVICESAttached logo was an example of what we wanted. Can you change up the colors?

Industry/Entity Type

Construction

Contact Information for Business Card

ROCK SOLID BUILDING SERVICES5401 HUDSON BEND RDAUSTIN, TX 78734(512)243-6854ROCKSOLIDBUILDINGSERVICES@GMAIL.COM

```html
<!DOCTYPE html>
<html lang="en">
<head>
<meta charset="utf-8">
<title>Pearlwood Framing Works – Business Card</title>
<link rel="stylesheet" href="https://fonts.googleapis.com/css2?family=Oswald:wght@600&family=Arimo:wght@400&display=swap">
<style>
  :root {
    --page-bg: #eeeff1;
    --card-white: #ffffff;
    --band-indigo: #2b1f6b;
    --panel-slate: #6a8aa1;
    --ink-dark: #111318;
    --ink-light: #ffffff;
  }
  * { margin: 0; padding: 0; box-sizing: border-box; }
  html, body {
    width: 1200px;
    height: 864px;
    overflow: hidden;
    background: var(--page-bg);
  }
  .card {
    position: absolute;
    left: 100px;
    top: 146px;
    width: 1000px;
    height: 571px;
    background: var(--card-white);
    box-shadow: 0 6px 24px rgba(0,0,0,0.12);
    overflow: hidden;
  }
  .card-shapes {
    position: absolute;
    inset: 0;
    width: 100%;
    height: 100%;
  }
  .shape-slate { fill: var(--panel-slate); }
  .shape-indigo { fill: var(--band-indigo); }

  .brand-mark {
    position: absolute;
    left: 40px;
    top: 220px;
    width: 330px;
    text-align: center;
    font-family: "Oswald", sans-serif;
    font-weight: 600;
    color: var(--band-indigo);
    line-height: 1.05;
  }
  .brand-mark .mark-name { font-size: 48px; letter-spacing: 1px; }
  .brand-mark .mark-tag { font-size: 24px; letter-spacing: 3px; }

  .company-title {
    position: absolute;
    left: 560px;
    top: 80px;
    width: 420px;
    text-align: center;
    color: var(--ink-light);
  }
  .company-title .title-name {
    font-family: "Oswald", sans-serif;
    font-weight: 600;
    font-size: 66px;
    line-height: 1;
    letter-spacing: 0.5px;
  }
  .company-title .title-sub {
    font-family: "Arimo", sans-serif;
    font-size: 18px;
    margin-top: 6px;
    letter-spacing: 0.5px;
  }

  .contact-list {
    position: absolute;
    right: 28px;
    top: 320px;
    width: 540px;
    list-style: none;
    font-family: "Arimo", sans-serif;
    font-size: 18px;
    color: var(--ink-dark);
    text-align: right;
  }
  .contact-list li { margin-bottom: 16px; }
  .contact-list .contact-phone { padding-right: 140px; }
  .contact-list .contact-address { padding-right: 20px; }
</style>
</head>
<body>
  <div class="card">
    <svg class="card-shapes" viewBox="0 0 1000 571" preserveAspectRatio="none" aria-hidden="true">
      <polygon class="shape-slate" points="280,0 1000,0 1000,571 345,571 510,270"/>
      <polygon class="shape-indigo" points="300,0 1000,0 1000,262 525,262"/>
    </svg>

    <div class="brand-mark">
      <div class="mark-name">PEARLWOOD</div>
      <div class="mark-tag">FRAMING WORKS</div>
    </div>

    <div class="company-title">
      <div class="title-name">PEARLWOOD</div>
      <div class="title-sub">FRAMING WORKS</div>
    </div>

    <ul class="contact-list">
      <li class="contact-phone">(512)555-0193</li>
      <li class="contact-address">7732 FERNGLEN PASS LN AUSTIN,TX 78734</li>
      <li class="contact-email">PEARLWOODFRAMINGWORKS@MAILNEST.EXAMPLE</li>
    </ul>
  </div>
</body>
</html>
```